A layout of a webpage for oil trade platform

I would like to have a desgin of one page webpage (with section scrollling dowin) that woulf present the new product i.e. oil trade platform for wholesale buyers and sellers.
Layout should consist of the sections similar to the given at: https://porada.leczmypol.pl/panel-planowania-spotkan
However oil industy require more colors and more photo stories than here for doctor.
I. I woul imagine at first below menu a slider with brueg information about the product and its advantages with "more" button next to the prict screen of our platform on different displays (PC and mobile).
II. Bellow the slider I would imagine icons correspoing to the advantages of that plaftorm:
1. Purchase/sale process automation 24/7
2. Access to the best deals
3. Electronic offerings and orderings
4. Transaction status monitoring
5. Data and transaction security
II A) (optional):
In near future we would like to prepare a short video presenation. Hence please prepare a place to display that element here.
At the moment alternatvily please prepare a How it works section that would explan the platform operating process
III. Next secion is about benefits for Oil Purchaser
It can be done either by icons of by text and corresponding grahip for while section.
Benefits:
- Access to cheaper oil
- Convenience of online orders
- Possibility to compare prices on the market
- Transaction history
- Order status monitoring
- Seccurity and transparency of purchase
IV. Next seciont is about benefits for Oil Seller
Benefits:
- New sale channel
- Attracting new clients
- More oil sold
- Transaction security
- Possibility to integrate with distribution infrastructure and logistits for more efficient automation.
V. Contact form
VI. Footer
I would need a layout that that will correspond to the very dynamic logo but I would expect also a clean form, smoth and modern. It has to be proffessional layout with more corporate character.
It can use a paralax features if needed.

```html
<!DOCTYPE html>
<html lang="en">
<head>
<meta charset="utf-8">
<title>Oleovia – Oil Trade Platform</title>
<link rel="stylesheet" href="https://fonts.googleapis.com/css2?family=Poppins:wght@300;400;500&family=Open+Sans:wght@400;600&display=swap">
<style>
  :root{
    --navy:#111c3a;
    --navy-deep:#0e1831;
    --orange:#e0582a;
    --ink:#1f2330;
    --text:#555a63;
    --muted:#8a8f98;
    --panel:#f0f0f0;
    --line:#cfd2d6;
    --white:#ffffff;
    --btn-dark:#333638;
  }
  *{box-sizing:border-box;margin:0;padding:0}
  html,body{width:1200px;height:2329px;overflow:hidden}
  body{font-family:"Open Sans",Arial,sans-serif;color:var(--text);background:var(--white);position:relative}
  .abs{position:absolute}

  /* header */
  .site-header{position:absolute;left:0;top:0;width:1200px;height:120px;background:var(--white)}
  .brand{position:absolute;left:132px;top:44px;display:flex;align-items:center;gap:12px}
  .brand-mark{width:30px;height:30px;border-radius:50%;background:var(--orange)}
  .brand-name{font-family:"Poppins",sans-serif;font-weight:500;font-size:26px;color:var(--navy);letter-spacing:.5px}
  .main-nav a{position:absolute;top:58px;font-family:"Poppins",sans-serif;font-size:12.5px;color:var(--ink);text-decoration:none}
  .main-nav a.active{color:var(--orange)}

  /* hero */
  .hero{position:absolute;left:0;top:120px;width:1200px;height:493px;background:var(--navy)}
  .hero-title{position:absolute;left:132px;top:68px;width:400px;font-family:"Poppins",sans-serif;font-weight:400;font-size:22px;line-height:32px;color:var(--white)}
  .hero-text{position:absolute;left:132px;top:175px;width:400px;font-size:9.5px;line-height:15px;color:#c3c8d4}
  .btn-outline{position:absolute;left:132px;top:254px;width:127px;height:42px;border:1px solid var(--white);color:var(--white);font-family:"Poppins",sans-serif;font-size:15px;display:flex;align-items:center;justify-content:center}
  .screen-desktop{position:absolute;left:562px;top:27px;width:638px;height:466px;background:linear-gradient(160deg,#2b3653 0%,#3a4563 40%,#0b0f1c 100%)}
  .screen-laptop{position:absolute;left:397px;top:268px;width:348px;height:193px;background:linear-gradient(160deg,#3a4563 0%,#242e48 60%,#0b0f1c 100%)}

  /* advantages */
  .advantages{position:absolute;left:0;top:613px;width:1200px;height:179px;background:var(--white)}
  .adv{position:absolute;top:32px;width:190px;text-align:center}
  .adv svg{width:56px;height:56px;stroke:#333;fill:none;stroke-width:1.4}
  .adv p{margin-top:18px;font-family:"Poppins",sans-serif;font-size:14px;line-height:22px;color:#3b3f47}

  /* split sections */
  .split{position:absolute;left:0;width:1200px;height:357px}
  .photo{position:absolute;top:0;width:600px;height:357px}
  .panel{position:absolute;top:0;width:600px;height:357px}
  .panel.grey{background:var(--panel)}
  .section-title{font-family:"Poppins",sans-serif;font-weight:400;font-size:25px;color:var(--orange)}
  .how-text{margin-top:12px;width:436px;font-size:10px;line-height:19px;color:#555}
  .btn-small{display:inline-block;margin-top:24px;width:81px;height:35px;border:1px solid #b9bcc0;font-size:10px;color:#444;line-height:33px;text-align:center;background:var(--white)}
  .benefits{list-style:none;margin-top:24px}
  .benefits li{display:flex;align-items:flex-start;font-family:"Poppins",sans-serif;font-size:15px;line-height:24px;color:var(--ink);margin-bottom:16px}
  .benefits svg{flex:0 0 14px;width:14px;height:14px;margin-top:5px;margin-right:28px;fill:var(--navy)}

  /* contact */
  .contact{position:absolute;left:0;top:1863px;width:1200px;height:369px;background:var(--white)}
  .contact .section-title{position:absolute;left:0;width:1200px;top:72px;text-align:center}
  .field{position:absolute;height:43px;border:1px solid var(--line);font-size:11px;color:#7c8088;padding-left:22px;display:flex;align-items:center}
  .field .chev{position:absolute;right:16px;top:15px;width:12px;height:12px;stroke:#777;fill:none;stroke-width:1.5}
  .btn-submit{position:absolute;left:559px;top:250px;width:81px;height:39px;background:var(--btn-dark);color:var(--white);font-size:12px;display:flex;align-items:center;justify-content:center}

  /* footer */
  .site-footer{position:absolute;left:0;top:2232px;width:1200px;height:97px;background:var(--navy-deep)}
  .footer-links{position:absolute;left:132px;top:26px;font-size:10px;color:#c3c8d4}
  .footer-links span.sep{margin:0 9px}
  .copyright{position:absolute;left:132px;top:54px;font-size:10px;color:#aeb4c2}
  .social{position:absolute;top:28px;width:38px;height:38px;border:1px solid #8d95a8;border-radius:50%}
</style>
</head>
<body>

<header class="site-header">
  <div class="brand"><span class="brand-mark"></span><span class="brand-name">Oleovia</span></div>
  <nav class="main-nav">
    <a class="active" style="left:627px">Home</a>
    <a style="left:700px">Advantages</a>
    <a style="left:807px">How it works</a>
    <a style="left:917px">Benefits</a>
    <a style="left:1000px">Contact Us</a>
  </nav>
</header>

<section class="hero">
  <div class="screen-desktop" role="img" aria-label="Platform order panel shown on desktop, tablet and phone screens"></div>
  <div class="screen-laptop" role="img" aria-label="Platform order panel shown on a laptop screen"></div>
  <h1 class="hero-title">Phasellus vestibulum, nulla rutrum porta, eros nulla semper risus, feugiat leo justo non dui.</h1>
  <p class="hero-text">Maecenas in efficitur tellus. Etiam mattis magna at tortor tincidunt mollis. Proin mi ante, pulvinar nec rhoncus cursus, mollis ac mi. Suspendisse ornare mattis pulvinar. Mauris augue nisi, mollis a ligula aliquam.</p>
  <div class="btn-outline">Learn More</div>
</section>

<section class="advantages">
  <div class="adv" style="left:124px">
    <svg viewBox="0 0 54 54"><circle cx="20" cy="30" r="7"/><path d="M20 16v5M20 39v5M6 30h5M29 30h5M10 20l4 4M26 36l4 4M30 20l-4 4M14 36l-4 4"/><circle cx="20" cy="30" r="12"/><circle cx="40" cy="16" r="4"/><circle cx="40" cy="16" r="8"/></svg>
    <p>Purchase/sale process<br>automation 24/7</p>
  </div>
  <div class="adv" style="left:315px">
    <svg viewBox="0 0 54 54"><path d="M8 30L30 8h14v14L22 44z"/><circle cx="37" cy="15" r="3"/><path d="M14 38l-4 4"/></svg>
    <p>Access to the<br>best deals</p>
  </div>
  <div class="adv" style="left:504px">
    <svg viewBox="0 0 54 54"><rect x="10" y="10" width="34" height="26"/><rect x="14" y="14" width="26" height="18"/><path d="M4 40h46l-3 4H7z"/></svg>
    <p>Electronic offerings and<br>orderings</p>
  </div>
  <div class="adv" style="left:695px">
    <svg viewBox="0 0 54 54"><rect x="12" y="8" width="30" height="40"/><rect x="21" y="5" width="12" height="6"/><path d="M18 20h18M18 27h18M18 34h18M18 41h12"/></svg>
    <p>Transaction status<br>monitoring</p>
  </div>
  <div class="adv" style="left:885px">
    <svg viewBox="0 0 54 54"><path d="M17 24v-7a10 10 0 0 1 20 0v7"/><rect x="11" y="24" width="32" height="24"/><path d="M11 30l8-6M11 38l14-14M15 48l24-24M25 48l18-14M35 48l8-6"/></svg>
    <p>Data and transaction<br>security</p>
  </div>
</section>

<section class="split" style="top:792px">
  <div class="photo" style="left:0;background:linear-gradient(180deg,#8a7c6f 0%,#c9a98a 45%,#5d6470 60%,#2f3a48 100%)" role="img" aria-label="Video placeholder: offshore oil platform at sea at dusk, with play button"></div>
  <svg class="abs" style="left:268px;top:155px" width="48" height="48" viewBox="0 0 48 48"><circle cx="24" cy="24" r="24" fill="#fff"/><path d="M19 14l15 10-15 10z" fill="#111"/></svg>
  <div class="panel grey" style="left:600px;padding:62px 0 0 32px">
    <h2 class="section-title">How it works</h2>
    <p class="how-text">Nulla elementum odio libero, sit amet blandit ipsum condimentum nec. Quisque vitae interdum neque. Vivamus tempus erat augue, non porta lorem egestas in. Nam elit massa, interdum at nisl quis, blandit sollicitudin justo. Ut lobortis vel mi vitae malesuada. Sed augue urna, consectetur eu ex et, vehicula ornare sem. Duis gravida dapibus diam sed euismod. Proin vel feugiat ligula. Curabitur vitae magna elit. Etiam sed feugiat orci, sit amet auctor ex. Aenean quam arcu, rutrum eu bibendum sit amet, gravida id nisl. Sed vulputate libero et pretium dictum. Aenean dapibus finibus congue.</p>
    <div class="btn-small">Read more</div>
  </div>
</section>

<section class="split" style="top:1149px">
  <div class="panel" style="left:0;padding:45px 0 0 129px">
    <h2 class="section-title">Benefits for Oil Purchaser</h2>
    <ul class="benefits">
      <li><svg viewBox="0 0 14 14"><path d="M7 1C5 5 3 7 3 9a4 4 0 0 0 8 0c0-2-2-4-4-8z"/></svg>Access to cheaper oil</li>
      <li><svg viewBox="0 0 14 14"><path d="M0 2h3l2 7h7l2-5H4.5l-.5-1.5z"/><circle cx="6" cy="12" r="1.3"/><circle cx="11" cy="12" r="1.3"/></svg>Convenience of online orders</li>
      <li><svg viewBox="0 0 14 14"><path d="M1 4h7v9H1zM2 5v7h5V5zM5 1h7v9h-3V9h2V2H6v1H5z"/></svg>Possibility to compare prices on the market</li>
      <li><svg viewBox="0 0 14 14"><path d="M7 1a6 6 0 1 1-5.6 8l1.5-.5A4.4 4.4 0 1 0 3.5 4L5 5.5H1v-4l1.4 1.4A6 6 0 0 1 7 1zM6.3 4h1.4v3.3l2 1.3-.7 1.1-2.7-1.7z"/></svg>Transaction history</li>
      <li><svg viewBox="0 0 14 14"><path d="M2 1h7l3 3v9H2zM3.3 2.3v9.4h7.4V5H8V2.3zM4.5 7h5v1h-5zM4.5 9h5v1h-5z"/></svg>Order status monitoring</li>
      <li><svg viewBox="0 0 14 14"><path d="M4 6V4.5a3 3 0 0 1 6 0V6h1v7H3V6zm1.4 0h3.2V4.5a1.6 1.6 0 0 0-3.2 0z"/></svg>Seccurity and transparency of purchase</li>
    </ul>
  </div>
  <div class="photo" style="left:600px;background:linear-gradient(135deg,#e3ddd4 0%,#cfc7bb 50%,#b9c2b0 100%)" role="img" aria-label="Black oil spilling from a barrel onto banknotes on a wooden table"></div>
</section>

<section class="split" style="top:1506px">
  <div class="photo" style="left:0;background:linear-gradient(120deg,#6e5b47 0%,#a89c8c 40%,#c9ccd0 70%,#8b94a0 100%)" role="img" aria-label="Two oil industry workers in hard hats holding plans at a refinery"></div>
  <div class="panel grey" style="left:600px;padding:45px 0 0 32px">
    <h2 class="section-title">Benefits for Oil Seller</h2>
    <ul class="benefits" style="width:400px">
      <li><svg viewBox="0 0 14 14"><path d="M1 5h3l7-4v12L4 9H3l1 4H2.5L1.5 9H1z"/></svg>New sale channel</li>
      <li><svg viewBox="0 0 14 14"><circle cx="5" cy="4" r="2.3"/><circle cx="10.5" cy="4.5" r="1.8"/><path d="M0 12c0-3 2-5 5-5s5 2 5 5zM10.5 7.5c2 0 3.5 1.5 3.5 4h-3c0-1.5-.5-3-1.5-3.8z"/></svg>Attracting new clients</li>
      <li><svg viewBox="0 0 14 14"><path d="M0 3h14v8H0zm1.3 1.3v5.4h11.4V4.3z"/><circle cx="7" cy="7" r="2"/></svg>More oil sold</li>
      <li><svg viewBox="0 0 14 14"><path d="M0 2h14v10H0zm1.3 1.3v1.4h11.4V3.3zm0 3.4v4h11.4v-4zM2.5 8.5h3v1h-3z"/></svg>Transaction security</li>
      <li><svg viewBox="0 0 14 14"><path d="M5.5 1h3v3h-1v2h5v3h1v3h-3V9h1V7H7.5v2h1v3h-3V9h1V7H2.5v2h1v3h-3V9h1V6h5V4h-1z"/></svg>Possibility to integrate with distribution infrastructure and logistits for more efficient automation.</li>
    </ul>
  </div>
</section>

<section class="contact">
  <h2 class="section-title">Contact Us</h2>
  <div class="field" style="left:132px;top:121px;width:217px">Name</div>
  <div class="field" style="left:371px;top:121px;width:217px">Email</div>
  <div class="field" style="left:610px;top:121px;width:217px">Phone</div>
  <div class="field" style="left:849px;top:121px;width:217px">When can we contact you?<svg class="chev" viewBox="0 0 12 12"><path d="M2 4l4 4 4-4"/></svg></div>
  <div class="field" style="left:132px;top:186px;width:934px">Message</div>
  <div class="btn-submit">SUBMIT</div>
</section>

<footer class="site-footer">
  <div class="footer-links">Home<span class="sep">|</span>Advantages<span class="sep">|</span>How it works<span class="sep">|</span>Benefits<span class="sep">|</span>Contact Us</div>
  <div class="copyright">Copyright © 2017 &nbsp;Company name. &nbsp;All rights reserved.</div>
  <span class="social" style="left:884px"></span>
  <span class="social" style="left:934px"></span>
  <span class="social" style="left:984px"></span>
  <span class="social" style="left:1034px"></span>
</footer>

</body>
</html>
```